Business card for Luxury Portable Restroom Trailer company

We are a Luxury Portable Restroom Trailer Company Called FALCRIDGE HIRES. Based in Orange County California. We provide portable restroom trailers for events, such as, Weddings, Concerts, Charity events, Sporting events, Tournaments, Corporate events, ect. We rent and Sell the Luxury restrooms. Our colors are white, grey, and Orange. As you will see in the logo we uploaded.
There are 2 people in the company so the names and titles will change for the 3 people but card will remain the same. Here is the information for each Person: Dwight Penner CFO 555 318-0476
next Person: Leon Marchetti VP 555 318-0476
Next Person: Owen Marchetti CEO 555 318-0476
Information to include on the card: Luxury Restroom Trailers Rental and Sales. Weddings, Concerts, Charity, Sporting and Corp. Events.

```html
<!DOCTYPE html>
<html lang="en">
<head>
<meta charset="utf-8">
<title>Falcridge Hires – Business Card</title>
<link href="https://fonts.googleapis.com/css2?family=Montserrat:wght@400;500;700;800&display=swap" rel="stylesheet">
<style>
  :root {
    --page: #e4e4e4;
    --card-dark: #2f3031;
    --card-light: #454748;
    --orange: #e0621f;
    --white: #f1f1f1;
    --grey-text: #d4d4d4;
    --ring: #808183;
  }
  * { margin: 0; padding: 0; box-sizing: border-box; }
  html, body { width: 1200px; height: 1200px; overflow: hidden; background: var(--page); }
  body { position: relative; font-family: "Montserrat", sans-serif; }

  .card {
    position: absolute;
    left: 234px;
    width: 731px;
    height: 418px;
    background: linear-gradient(135deg, var(--card-dark) 0%, var(--card-dark) 45%, var(--card-light) 100%);
  }
  .card--front { top: 160px; }
  .card--back { top: 632px; }

  /* Front */
  .front-ring {
    position: absolute;
    left: 294px; top: 105px;
    width: 142px; height: 142px;
    border-radius: 50%;
    border: 5px solid var(--ring);
  }
  .front-name {
    position: absolute;
    left: 0; right: 0; top: 262px;
    text-align: center;
    font-weight: 800;
    font-size: 50px;
    letter-spacing: 1px;
    color: var(--orange);
    line-height: 1;
  }

  /* Back */
  .back-brand {
    position: absolute;
    left: 74px; width: 262px; top: 160px;
    text-align: center;
    font-weight: 800;
    font-size: 25px;
    letter-spacing: 0.5px;
    color: var(--white);
    line-height: 1.1;
  }
  .divider {
    position: absolute;
    left: 366px; top: 109px;
    width: 2px; height: 147px;
    background: var(--grey-text);
  }
  .person {
    position: absolute;
    left: 399px; top: 106px;
  }
  .person__name {
    font-weight: 700;
    font-size: 30px;
    color: var(--orange);
    line-height: 1.1;
  }
  .person__title {
    font-weight: 400;
    font-size: 19px;
    color: var(--grey-text);
    margin-top: 2px;
  }
  .contacts {
    list-style: none;
    margin-top: 17px;
  }
  .contacts li {
    display: flex;
    align-items: center;
    gap: 10px;
    height: 28px;
    font-size: 19px;
    color: var(--grey-text);
  }
  .contacts svg { width: 16px; height: 16px; flex: none; }

  .tagline {
    position: absolute;
    left: 0; right: 0; top: 329px;
    text-align: center;
    font-weight: 700;
    font-size: 18px;
    color: var(--orange);
  }
  .events {
    position: absolute;
    left: 0; right: 0; top: 356px;
    text-align: center;
    font-weight: 400;
    font-size: 18px;
    color: var(--grey-text);
  }
  .events .sep { color: var(--orange); padding: 0 4px; }
</style>
</head>
<body>

<section class="card card--front">
  <div class="front-ring"></div>
  <div class="front-name">FALCRIDGE</div>
</section>

<section class="card card--back">
  <div class="back-brand">FALCRIDGE HIRES</div>
  <div class="divider"></div>

  <div class="person">
    <div class="person__name">Dwight Penner</div>
    <div class="person__title">CFO</div>
    <ul class="contacts">
      <li>
        <svg viewBox="0 0 24 24" aria-hidden="true"><path fill="#e0621f" d="M6.6 10.8a15.1 15.1 0 0 0 6.6 6.6l2.2-2.2a1 1 0 0 1 1-.25 11.4 11.4 0 0 0 3.6.57 1 1 0 0 1 1 1V20a1 1 0 0 1-1 1A17 17 0 0 1 3 4a1 1 0 0 1 1-1h3.5a1 1 0 0 1 1 1c0 1.25.2 2.45.57 3.57a1 1 0 0 1-.25 1z"/></svg>
        555 318-0476
      </li>
      <li>
        <svg viewBox="0 0 24 24" aria-hidden="true"><rect x="2" y="5" width="20" height="14" rx="1.5" fill="#e0621f"/><path d="M3 6l9 7 9-7" fill="none" stroke="#2f3031" stroke-width="1.6"/></svg>
        info@falcridgehires.com
      </li>
      <li>
        <svg viewBox="0 0 24 24" aria-hidden="true"><g fill="none" stroke="#e0621f" stroke-width="2"><circle cx="12" cy="12" r="9.5"/><ellipse cx="12" cy="12" rx="4" ry="9.5"/><path d="M2.5 12h19"/></g></svg>
        www.falcridgehires.com
      </li>
    </ul>
  </div>

  <div class="tagline">Luxury Restroom Trailers Rental and Sales</div>
  <div class="events">Weddings<span class="sep">|</span>Concerts<span class="sep">|</span>Charity<span class="sep">|</span>Sporting<span class="sep">|</span>Corp. Events</div>
</section>

</body>
</html>
```